Mental Health Clinic Website

website for a mental health clinic. two files describing the website are attached, in case of conflicting info the word document is priority.

Target Market(s)

Ohio / Pennsylvania residents

Industry/Entity Type

Health Care

Coding

Coded - Design and coding required

Number of Pages Required

5+ page

Requirements
Must have
• see attached

```html
<!DOCTYPE html>
<html lang="en">
<head>
<meta charset="utf-8">
<title>Dr Ravelle Serenity Center</title>
<link href="https://fonts.googleapis.com/css2?family=Montserrat:wght@500;600;700&family=Open+Sans:wght@400;600;700&display=swap" rel="stylesheet">
<style>
:root{
  --blue:#1d55b4;
  --blue-dark:#15408c;
  --blue-deep:#0f2f6a;
  --green:#3f9a2c;
  --green-light:#5bb53f;
  --ink:#2b2b2b;
  --muted:#6f6f6f;
  --line:#d9d9d9;
  --white:#ffffff;
  --paper:#f6f7f9;
}
*{box-sizing:border-box;margin:0;padding:0}
html,body{width:1200px;height:4904px;overflow:hidden}
body{position:relative;background:var(--white);font-family:"Open Sans",Arial,sans-serif;color:var(--ink)}
.abs{position:absolute}
h1,h2,h3,h4{font-family:"Montserrat",Arial,sans-serif}

/* top bar */
.topbar{left:0;top:0;width:1200px;height:32px;background:var(--blue);color:var(--white);font-size:12px;display:flex;align-items:center;padding:0 40px;gap:0}
.topbar .addr{flex:1}
.topbar span{display:inline-flex;align-items:center;gap:6px;margin-left:28px}
.topbar svg{width:12px;height:12px;fill:var(--white)}

/* header */
.header{left:0;top:32px;width:1200px;height:128px;background:var(--white);display:flex;align-items:center;padding:0 40px}
.brand{display:flex;align-items:center;gap:10px;width:300px}
.brand-dot{width:30px;height:30px;border-radius:50%;background:var(--green)}
.brand-name{font-family:"Montserrat",Arial,sans-serif;font-weight:600;font-size:15px;color:var(--blue)}
.nav{margin-left:auto;display:flex;gap:26px;font-family:"Montserrat",Arial,sans-serif;font-weight:600;font-size:15px;color:var(--ink)}

/* hero */
.hero{left:0;top:160px;width:1200px;height:700px;background:linear-gradient(180deg,#4b6f93 0%,#8fb0c9 24%,#3d5b3a 48%,#6e8f6c 62%,#2f6c8a 78%,#1b3e4f 100%)}
.hero-title{right:70px;top:330px;width:520px;text-align:right;color:var(--white);font-family:"Montserrat",Arial,sans-serif;font-weight:600;font-size:46px;line-height:1.15;letter-spacing:1px}
.hero-btn{left:595px;top:436px;height:46px;padding:0 24px;background:var(--blue);color:var(--white);border-radius:3px;font-family:"Montserrat",Arial,sans-serif;font-weight:700;font-size:15px;display:flex;align-items:center;gap:8px}
.hero-arrow{top:470px;width:20px;height:20px;color:var(--white);font-size:22px;line-height:20px}
.wave{left:0;width:1200px}

/* welcome */
.section-title{left:0;width:1200px;text-align:center;font-family:"Montserrat",Arial,sans-serif;font-weight:600;font-size:40px;color:var(--ink)}
.welcome-text{left:185px;top:1036px;width:830px;text-align:center;font-size:14px;line-height:1.7;color:var(--muted)}
.welcome-text p{margin-bottom:22px}

/* about */
.about-photo{left:112px;top:1372px;width:416px;height:390px;background:linear-gradient(180deg,#e7a646 0%,#c9752d 50%,#6d4423 100%)}
.about-box{left:552px;top:1352px;width:536px;height:400px;background:var(--blue);color:var(--white);padding:44px 40px;font-size:14px;line-height:1.7}
.about-box h3{font-size:36px;font-weight:700;margin-bottom:8px;border-bottom:2px solid rgba(255,255,255,.5);display:inline-block;padding-bottom:4px}
.about-box p{margin-bottom:12px}
.langs{display:grid;grid-template-columns:200px 200px;margin-top:10px;gap:6px}
.langs li{list-style:none}
.langs li:before{content:"• ";}

/* team */
.team-band{left:0;top:2040px;width:1200px;height:680px;background:linear-gradient(180deg,var(--green-light),var(--green))}
.team-row{left:140px;top:2240px;width:920px;display:flex;justify-content:space-between}
.team-card{width:208px;height:320px;background:var(--white);padding:22px 16px;text-align:center;box-shadow:0 3px 10px rgba(0,0,0,.2)}
.team-photo{width:92px;height:92px;border-radius:50%;margin:0 auto 14px;background:linear-gradient(160deg,#d9c9b8,#8c7564);border:4px solid var(--white);box-shadow:0 0 0 1px var(--line)}
.team-card h4{font-size:19px;font-weight:600;color:var(--ink)}
.team-role{font-size:12px;color:var(--muted);margin-bottom:8px}
.team-card p{font-size:12px;line-height:1.5;color:var(--muted);margin-bottom:16px}
.appt-btn{display:inline-block;background:var(--blue);color:var(--white);font-size:12px;font-weight:700;padding:8px 16px;border-radius:2px}
.team-nav{top:2628px;width:48px;height:48px;border-radius:50%;border:2px solid var(--white);color:var(--white);font-size:22px;display:flex;align-items:center;justify-content:center}

/* services */
.services-title{left:540px;top:2848px;width:660px;text-align:center;font-weight:600;font-size:40px}
.services-row{left:110px;top:2990px;width:980px;display:flex;justify-content:space-between}
.service{width:170px;text-align:center}
.service-icon{width:120px;height:120px;margin:0 auto 18px;border-radius:50%;border:2px solid var(--line);display:flex;align-items:center;justify-content:center;background:var(--white)}
.service-icon svg{width:56px;height:56px;stroke:var(--blue);fill:none;stroke-width:3}
.service.active .service-icon{background:var(--green);border-color:var(--green);width:150px;height:150px;margin-top:-30px}
.service.active .service-icon svg{stroke:var(--white)}
.service-label{font-family:"Montserrat",Arial,sans-serif;font-weight:700;font-size:16px;color:var(--ink);padding-bottom:10px;border-bottom:3px solid transparent}
.service.active .service-label{border-bottom-color:var(--green)}
.art-photo{left:112px;top:3284px;width:448px;height:240px;background:linear-gradient(120deg,#e5e1d9 0%,#c95a3e 35%,#3e7fc3 60%,#f0c84a 85%)}
.art-text{left:640px;top:3290px;width:440px}
.art-text h3{font-size:36px;font-weight:600;margin-bottom:18px}
.art-text p{font-size:14px;line-height:1.7;color:var(--muted);margin-bottom:24px}
.green-btn{display:inline-flex;align-items:center;gap:8px;background:var(--green);color:var(--white);font-family:"Montserrat",Arial,sans-serif;font-weight:700;font-size:14px;padding:12px 22px;border-radius:2px}

/* good reads */
.reads-intro{left:380px;top:3890px;width:440px;text-align:center;font-size:13px;line-height:1.6;color:var(--muted)}
.read-card{top:3960px;width:468px;height:220px;background:var(--white);box-shadow:0 2px 10px rgba(0,0,0,.15);display:flex}
.read-img{width:200px;height:220px}
.read-body{padding:20px 22px}
.read-body h4{font-size:20px;font-weight:700}
.read-author{font-size:11px;font-weight:700;color:var(--green);margin:4px 0 10px}
.read-body p{font-size:12px;line-height:1.6;color:var(--muted)}

/* footer */
.footer{left:0;top:4360px;width:1200px;height:544px;background:var(--blue)}
.foot-col h4{color:var(--white);font-size:15px;font-weight:700;margin-bottom:18px}
.form-field{width:330px;height:32px;border:1px solid rgba(255,255,255,.55);margin-bottom:10px;color:rgba(255,255,255,.8);font-size:12px;padding:0 10px;display:flex;align-items:center}
.submit{display:inline-block;background:var(--green);color:var(--white);font-weight:700;font-size:12px;padding:8px 18px;border-radius:12px;margin-top:10px}
.contact-line{display:flex;gap:10px;color:var(--white);font-size:13px;line-height:1.5;margin-bottom:14px}
.contact-line svg{width:16px;height:16px;fill:var(--white);flex:none;margin-top:2px}
.map{left:840px;top:4580px;width:300px;height:190px;background:linear-gradient(135deg,#eef0ea,#d6e2cf 50%,#cbd8e6)}
.socials{left:820px;top:4800px;display:flex;gap:10px}
.socials i{display:block;width:32px;height:32px;border-radius:50%;border:1px solid rgba(255,255,255,.7)}
.copyright{left:0;top:4856px;width:1200px;height:48px;background:var(--blue-deep);color:rgba(255,255,255,.8);font-size:12px;display:flex;align-items:center;padding:0 40px;justify-content:space-between}
</style>
</head>
<body>

<div class="abs topbar">
  <div class="addr"><span style="margin-left:0"><svg viewBox="0 0 24 24"><path d="M12 2a7 7 0 0 0-7 7c0 5 7 13 7 13s7-8 7-13a7 7 0 0 0-7-7zm0 9.5A2.5 2.5 0 1 1 12 6.5a2.5 2.5 0 0 1 0 5z"/></svg>2150 Maple Crest Drive, Suite 210, Hudson, OH 44236</span></div>
  <span><svg viewBox="0 0 24 24"><path d="M6.6 10.8a15 15 0 0 0 6.6 6.6l2.2-2.2c.3-.3.7-.4 1-.2 1.1.4 2.3.6 3.6.6.6 0 1 .4 1 1V20c0 .6-.4 1-1 1A17 17 0 0 1 3 4c0-.6.4-1 1-1h3.5c.6 0 1 .4 1 1 0 1.3.2 2.5.6 3.6.1.3 0 .7-.2 1z"/></svg>(330) 555-0142</span>
  <span><svg viewBox="0 0 24 24"><path d="M2 5h20v14H2zm2 2v.5l8 5 8-5V7z"/></svg>care@ravelleserenity.com</span>
</div>

<header class="abs header">
  <div class="brand"><span class="brand-dot"></span><span class="brand-name">Dr Ravelle Serenity Center</span></div>
  <nav class="nav"><span>Home</span><span>About Us</span><span>Services</span><span>Treatment</span><span>Good Reads</span><span>Languages Spoken</span><span>Contact Us</span></nav>
</header>

<section class="abs hero" role="img" aria-label="Photo of a calm mountain lake at sunrise with pine trees"></section>
<div class="abs hero-arrow" style="left:40px">‹</div>
<div class="abs hero-arrow" style="left:1140px">›</div>
<h1 class="abs hero-title">DR RAVELLE SERENITY CENTER</h1>
<div class="abs hero-btn" style="left:auto;right:405px;top:580px">READ MORE <span>›</span></div>
<svg class="abs wave" style="top:760px" width="1200" height="100" viewBox="0 0 1200 100" preserveAspectRatio="none"><path d="M0 40 C300 110 500 110 700 60 S1050 0 1200 50 V100 H0Z" fill="#fff"/></svg>

<h2 class="abs section-title" style="top:955px">WELCOME TO OUR CENTER</h2>
<div class="abs welcome-text">
  <p>From the first visit to recovery, every person brings a unique story and unique needs. Therefore we provide individual treatment customized for each person. We are a full service mental health practice with the capacity to serve adults, children, teens and their parents.</p>
  <p>We provide high quality evidence based treatment and care including medication management, pharmacogenetic testing, individual psychotherapy, group psychotherapy, art therapy, CBT, DBT and trauma therapy. Our providers are experts in treating a variety of disorders such as depression, anxiety, schizophrenia, ADHD, gender identity concerns and PTSD.</p>
  <p>We are experienced in a variety of methods that help people achieve their psychological goals, and we will discuss with you the best ways to obtain the health and wellness that you deserve. We are committed to helping you achieve your optimal level of emotional functioning and fulfill a successful life.</p>
</div>

<div class="abs about-photo" role="img" aria-label="Photo of a woman in a yoga pose at sunset"></div>
<div class="abs about-box">
  <h3>ABOUT US</h3>
  <p>You will find a number of highly specialized, experienced and caring therapists and psychiatrists at our center. We provide medication management and psychotherapy (counseling) across the lifespan.</p>
  <p>– children, teens and adults</p>
  <p style="font-weight:600">We speak the following languages:</p>
  <ul class="langs"><li>Spanish</li><li>Farsi</li><li>German</li><li>Hebrew</li></ul>
</div>

<svg class="abs wave" style="top:1960px" width="1200" height="120" viewBox="0 0 1200 120" preserveAspectRatio="none"><path d="M0 80 C250 0 500 0 750 60 S1100 120 1200 40 V120 H0Z" fill="#4faa36"/></svg>
<div class="abs team-band"></div>
<svg class="abs wave" style="top:2700px" width="1200" height="120" viewBox="0 0 1200 120" preserveAspectRatio="none"><path d="M0 40 C300 120 550 100 800 50 S1100 20 1200 70 V120 H0Z" fill="#fff"/></svg>

<div class="abs team-row">
  <div class="team-card"><div class="team-photo" role="img" aria-label="Portrait photo of Olivia Emily"></div><h4>Olivia Emily</h4><div class="team-role">Founder</div><p>Lorem ipsum dolor sit consectetur adipiscing elit sed do eiusmod tempor</p><span class="appt-btn">Make Appointment</span></div>
  <div class="team-card"><div class="team-photo" role="img" aria-label="Portrait photo of Sophia Emma"></div><h4>Sophia Emma</h4><div class="team-role">Co-Founder</div><p>Lorem ipsum dolor sit consectetur adipiscing elit sed do eiusmod tempor</p><span class="appt-btn">Make Appointment</span></div>
  <div class="team-card"><div class="team-photo" role="img" aria-label="Portrait photo of Mia Charlotte"></div><h4>Mia Charlotte</h4><div class="team-role">Manager</div><p>Lorem ipsum dolor sit consectetur adipiscing elit sed do eiusmod tempor</p><span class="appt-btn">Make Appointment</span></div>
  <div class="team-card"><div class="team-photo" role="img" aria-label="Portrait photo of Abigail Emily"></div><h4>Abigail Emily</h4><div class="team-role">Head Manager</div><p>Lorem ipsum dolor sit consectetur adipiscing elit sed do eiusmod tempor</p><span class="appt-btn">Make Appointment</span></div>
</div>
<div class="abs team-nav" style="left:118px">‹</div>
<div class="abs team-nav" style="left:186px">›</div>

<h2 class="abs services-title">OUR SERVICES</h2>
<div class="abs services-row">
  <div class="service"><div class="service-icon"><svg viewBox="0 0 56 56"><circle cx="28" cy="28" r="5"/><ellipse cx="28" cy="28" rx="22" ry="9"/><ellipse cx="28" cy="28" rx="22" ry="9" transform="rotate(60 28 28)"/><ellipse cx="28" cy="28" rx="22" ry="9" transform="rotate(-60 28 28)"/></svg></div><div class="service-label">MEDICATION</div></div>
  <div class="service"><div class="service-icon"><svg viewBox="0 0 56 56"><path d="M18 48V38c-6-4-8-10-8-16a16 16 0 0 1 32 0l4 8h-4v8h-8v10"/><circle cx="27" cy="22" r="6"/></svg></div><div class="service-label">PSYCHOTHERAPY</div></div>
  <div class="service active"><div class="service-icon"><svg viewBox="0 0 56 56"><path d="M20 48V38c-6-4-8-10-8-16a16 16 0 0 1 32 0l4 8h-4v8h-8v10"/><path d="M22 16l10 10M32 16l-10 10"/></svg></div><div class="service-label">ART THERAPY</div></div>
  <div class="service"><div class="service-icon"><svg viewBox="0 0 56 56"><circle cx="28" cy="28" r="10"/><path d="M28 6v10M28 40v10M6 28h10M40 28h10M13 13l7 7M36 36l7 7M43 13l-7 7M20 36l-7 7"/></svg></div><div class="service-label">OUR APPROACH</div></div>
  <div class="service"><div class="service-icon"><svg viewBox="0 0 56 56"><path d="M6 40h12l10 6 20-10-4-4-14 6M18 40V30h10l8 4"/><path d="M34 10c-4 0-6 4-6 6 0 5 6 9 6 9s6-4 6-9c0-2-2-6-6-6z"/></svg></div><div class="service-label">TREATMENT AREAS</div></div>
</div>

<div class="abs art-photo" role="img" aria-label="Photo of a colourful painting on an easel with an art therapy sign"></div>
<div class="abs art-text">
  <h3>ART THERAPY</h3>
  <p>Lorem ipsum dolor sit amet, consectetur adipiscing elit, sed do eiusmod tempor incididunt ut labore et dolore magna aliqua. Ut enim ad minim veniam, quis nostrud exercitation ullamco laboris nisi ut aliquip ex ea commodo consequat. Duis aute irure dolor in reprehenderit in voluptate velit esse cillum dolore eu fugiat nulla pariatur.</p>
  <span class="green-btn">READ MORE <span>›</span></span>
</div>

<h2 class="abs section-title" style="top:3820px">GOOD READS</h2>
<p class="abs reads-intro">Lorem ipsum dolor sit amet, consectetur adipiscing elit, sed do eiusmod tempor incididunt ut labore et dolore magna aliqua.</p>
<div class="abs read-card" style="left:112px">
  <div class="read-img" role="img" aria-label="Photo of an open book" style="background:linear-gradient(160deg,#d8c7a4,#8a6a3f)"></div>
  <div class="read-body"><h4>TITLE HERE</h4><div class="read-author">AUTHOR NAME HERE</div><p>At vero eos et accusam et justo duo dolores et ea rebum. Stet clita kasd gubergren, no sea takimata.</p></div>
</div>
<div class="abs read-card" style="left:612px">
  <div class="read-img" role="img" aria-label="Photo of books on a shelf" style="background:linear-gradient(160deg,#8a3a2a,#3b2a24)"></div>
  <div class="read-body"><h4>TITLE HERE</h4><div class="read-author">AUTHOR NAME HERE</div><p>At vero eos et accusam et justo duo dolores et ea rebum. Stet clita kasd gubergren, no sea takimata.</p></div>
</div>

<svg class="abs wave" style="top:4290px" width="1200" height="80" viewBox="0 0 1200 80" preserveAspectRatio="none"><path d="M0 50 C300 0 600 0 900 40 S1150 60 1200 30 V80 H0Z" fill="#1d55b4"/></svg>
<footer class="abs footer"></footer>
<div class="abs foot-col" style="left:112px;top:4420px">
  <h4>APPOINTMENT REQUEST</h4>
  <div class="form-field">First Name</div>
  <div class="form-field">Last Name</div>
  <div class="form-field">Email</div>
  <div class="form-field">Tel</div>
  <span class="submit">SUBMIT</span>
</div>
<div class="abs foot-col" style="left:510px;top:4530px;width:280px">
  <h4>CONTACT US</h4>
  <div class="contact-line"><svg viewBox="0 0 24 24"><path d="M12 2a7 7 0 0 0-7 7c0 5 7 13 7 13s7-8 7-13a7 7 0 0 0-7-7zm0 9.5A2.5 2.5 0 1 1 12 6.5a2.5 2.5 0 0 1 0 5z"/></svg><span>2150 Maple Crest Drive, Suite 210, Hudson, OH 44236</span></div>
  <div class="contact-line"><svg viewBox="0 0 24 24"><path d="M6.6 10.8a15 15 0 0 0 6.6 6.6l2.2-2.2c.3-.3.7-.4 1-.2 1.1.4 2.3.6 3.6.6.6 0 1 .4 1 1V20c0 .6-.4 1-1 1A17 17 0 0 1 3 4c0-.6.4-1 1-1h3.5c.6 0 1 .4 1 1 0 1.3.2 2.5.6 3.6.1.3 0 .7-.2 1z"/></svg><span>(330) 555-0142</span></div>
  <div class="contact-line"><svg viewBox="0 0 24 24"><path d="M2 5h20v14H2zm2 2v.5l8 5 8-5V7z"/></svg><span>care@ravelleserenity.com</span></div>
</div>
<div class="abs map" role="img" aria-label="Street map showing the center's location"></div>
<div class="abs socials"><i></i><i></i><i></i><i></i></div>
<div class="abs copyright"><span>Copyright © 2019 Dr Ravelle Serenity Center . All Rights Reserved</span><span>Site</span></div>

</body>
</html>
```